Help design website for "Brightwater Civic Advisors" to advance the common good

Here is the Google doc link that lays out the design:

https://files.plumrivet.example/sheet/d/7QmTzR2wLx9KpVbN4hJcY8sEaUoFdG3iXkMnPq5rWt6/edit?usp=sharing

Here is the Google drive folder with the logos and photos: https://vault.plumrivet.example/open?id=4HkWp9LzQe2TxRvN8mBaYc3DsUoJfG6

The testimonials are being gathered and will be shared by Friday, 1/4.

The winner will also have to migrate the coding files to my hosting site.

Thank you for your help! Looking forward to seeing your designs.

Target Market(s)

Prospective clients

Industry/Entity Type

Non Profit

Coding

Coded - Design and coding required

Number of Pages Required

5+ page

Requirements
Must have
• Noted in the Google doc regarding layout.
Nice to have

```html
<!DOCTYPE html>
<html lang="en">
<head>
<meta charset="utf-8">
<title>Brightwater Civic Advisors</title>
<link rel="stylesheet" href="https://fonts.googleapis.com/css2?family=Jost:wght@400;500&family=Roboto:ital,wght@0,400;0,500;1,400;1,500&display=swap">
<style>
:root{
  --blue:#3a8fd9;
  --blue-dark:#2f78bd;
  --navy:#262a36;
  --navy-deep:#1f232d;
  --ink:#333844;
  --muted:#666b74;
  --light:#f2f2f2;
  --white:#ffffff;
  --line:#d9dce1;
}
*{box-sizing:border-box;margin:0;padding:0}
html,body{width:1200px;height:4615px;overflow:hidden}
body{font-family:"Roboto",Arial,sans-serif;color:var(--ink);background:var(--white)}
.section{position:relative;width:1200px;overflow:hidden}
.abs{position:absolute}
.heading{font-family:"Jost",Arial,sans-serif;font-weight:400;text-align:center;width:100%;font-size:40px}
.rule{position:absolute;left:570px;width:60px;height:3px;background:var(--blue)}
.btn{position:absolute;display:flex;align-items:center;justify-content:center;border-radius:30px;font-size:16px}
.btn-solid{background:var(--blue);color:var(--white)}
.btn-outline{border:2px solid var(--blue);color:var(--blue)}

/* hero */
.hero{height:745px;background:linear-gradient(160deg,#4b4e4a 0%,#2e3230 45%,#3c3a35 75%,#2a2b2c 100%)}
.hero-photo{position:absolute;inset:0;background:linear-gradient(180deg,rgba(20,22,24,.25),rgba(20,22,24,.55))}
.topbar{left:143px;top:40px;color:var(--white);font-size:17px;display:flex;align-items:center;gap:12px}
.nav{left:143px;top:82px;display:flex;gap:22px;color:var(--white);font-size:19px}
.brand{left:800px;top:42px;display:flex;align-items:center;gap:14px;color:var(--white)}
.brand-mark{width:52px;height:52px;border:3px solid var(--white)}
.brand-name{font-family:"Jost",Arial,sans-serif;font-weight:400;font-size:19px;letter-spacing:4px;line-height:22px;text-transform:uppercase}
.brand-tag{font-family:"Jost",Arial,sans-serif;font-size:9px;letter-spacing:2px;text-transform:uppercase}
.hero-title{top:318px;color:var(--white);font-size:52px;font-weight:500}
.hero-sub{left:280px;width:640px;top:392px;color:var(--white);text-align:center;font-size:16px;line-height:26px}
.hero-arrow{top:375px;width:30px;height:30px}
.hero-notch{left:520px;bottom:0;width:160px;height:40px}

/* welcome */
.welcome{height:578px}
.welcome-kicker{left:143px;top:105px;font-family:"Jost",sans-serif;font-size:32px;color:#4a4f58}
.welcome-title{left:143px;top:145px;font-family:"Jost",sans-serif;font-size:37px;color:var(--blue)}
.welcome-text{left:143px;top:210px;width:430px;font-size:13.5px;line-height:23px;color:#444}
.portrait-frame{left:603px;top:105px;width:452px;height:367px;border:5px solid var(--blue);border-right:none;border-bottom:none}
.portrait{left:613px;top:115px;width:442px;height:357px;background:linear-gradient(135deg,#8a7a6a,#c7b39c 50%,#5b4c41)}

/* services */
.services{height:892px;background:linear-gradient(180deg,var(--navy) 0%,#2c3140 100%);color:var(--white)}
.svc-icons{top:226px;left:0;width:1200px;height:160px}
.svc{position:absolute;width:220px;text-align:center;font-size:17px;line-height:24px}
.svc-circle{width:90px;height:90px;border-radius:50%;border:2px solid var(--white);margin:0 auto 14px;display:flex;align-items:center;justify-content:center}
.svc-circle.active{background:var(--blue);border-color:var(--blue)}
.svc-nav{top:280px;width:32px;height:32px;border:1.5px solid #9aa0ab;border-radius:50%;display:flex;align-items:center;justify-content:center}
.feature-frame{left:143px;top:477px;width:425px;height:245px;border:5px solid var(--blue);border-right:none;border-bottom:none}
.feature-photo{left:151px;top:485px;width:417px;height:237px;background:linear-gradient(135deg,#5e5f66,#8c7f77 50%,#3e3f47)}
.feature-title{left:615px;top:490px;font-family:"Jost",sans-serif;font-size:31px}
.feature-text{left:615px;top:545px;width:440px;font-size:14px;line-height:24px;color:#d6d9df}
.services .btn-outline{border-color:var(--white);color:var(--white)}

/* testimonials */
.testimonials{height:462px;background:var(--light)}
.quote{position:absolute;width:330px}
.avatar{position:absolute;width:120px;height:120px;border-radius:50%;background:linear-gradient(135deg,#9fa3a8,#d4cfc8)}
.quote-text{font-style:italic;font-size:15px;line-height:24px;color:#333}
.stars{color:var(--blue);font-size:15px;letter-spacing:2px;margin:4px 0 10px}
.quote-name{font-style:italic;font-weight:500;font-size:15px}
.qmark{position:absolute;font-family:"Jost",sans-serif;font-size:60px;color:var(--blue);line-height:1}

/* media */
.media{height:738px;background:linear-gradient(180deg,#fff 0%,#fff 60%,#f3f5f8 100%)}
.card{position:absolute;background:var(--white);box-shadow:0 2px 10px rgba(0,0,0,.12)}
.card-photo{position:absolute;background:linear-gradient(135deg,#6f6a62,#a89a86 50%,#4a4a48)}
.card-title{font-family:"Jost",sans-serif;font-size:19px;line-height:24px;color:#3a3f48}
.card-meta{font-size:12.5px;color:var(--blue);font-style:italic;margin:8px 0}
.card-meta span{margin-right:22px}
.card-text{font-size:13px;line-height:20px;color:#555}

/* partners */
.partners{height:385px;background:var(--white)}
.badge{position:absolute;background:#e4e7ec}

/* contact */
.contact{height:600px;background:var(--navy-deep);color:var(--white)}
.contact-notch{left:555px;top:0;width:90px;height:32px}
.info-row{position:absolute;left:145px;display:flex;gap:24px;align-items:flex-start;font-size:15px;line-height:22px}
.info-icon{width:42px;height:42px;border-radius:50%;border:2px solid var(--white);display:flex;align-items:center;justify-content:center;flex:none}
.field{position:absolute;border:1px solid #6b717d;font-size:13px;padding:10px 12px;color:#e6e8ec}

/* footer */
.footer{height:215px;background:#f6f6f6;text-align:center}
.foot-links{top:60px;width:100%;font-size:16px;color:#333}
.foot-copy{top:92px;width:100%;font-size:16px;color:#333}
.social{position:absolute;top:128px;width:30px;height:30px;border-radius:50%;border:2px solid var(--blue)}
</style>
</head>
<body>

<section class="section hero">
  <div class="hero-photo" role="img" aria-label="Group photo of smiling young program participants outdoors"></div>
  <div class="abs topbar">
    <svg width="18" height="18" viewBox="0 0 24 24" fill="#fff"><path d="M6.6 10.8a15.1 15.1 0 0 0 6.6 6.6l2.2-2.2a1 1 0 0 1 1-.25 11.4 11.4 0 0 0 3.6.57 1 1 0 0 1 1 1V20a1 1 0 0 1-1 1A17 17 0 0 1 3 4a1 1 0 0 1 1-1h3.5a1 1 0 0 1 1 1c0 1.25.2 2.45.57 3.57a1 1 0 0 1-.25 1z"/></svg>
    <span>Call Us +000 5550 1234</span>
  </div>
  <nav class="abs nav"><span>Home</span><span>About</span><span>Services &amp; Testimonials</span><span>Media &amp; Impact</span><span>Contact</span></nav>
  <div class="abs brand">
    <div class="brand-mark"></div>
    <div>
      <div class="brand-name">Brightwater<br>Civic Advisors</div>
      <div class="brand-tag">Advancing the common good</div>
    </div>
  </div>
  <h1 class="abs heading hero-title">Brightwater Civic Advisors</h1>
  <p class="abs hero-sub">Sed ut perspiciatis unde omnis iste natus error sit voluptatem accusantium doloremque laudantium, totam rem aperiam, eaque ipsa quae</p>
  <div class="btn btn-solid" style="left:510px;top:470px;width:180px;height:46px;font-size:18px">Learn More</div>
  <svg class="abs hero-arrow" style="left:110px" viewBox="0 0 30 30"><path d="M18 7l-8 8 8 8" stroke="#fff" stroke-width="3" fill="none"/></svg>
  <svg class="abs hero-arrow" style="left:1060px" viewBox="0 0 30 30"><path d="M12 7l8 8-8 8" stroke="#fff" stroke-width="3" fill="none"/></svg>
  <svg class="abs hero-notch" viewBox="0 0 160 40"><path d="M0 40 C40 40 55 0 80 0 C105 0 120 40 160 40Z" fill="#fff"/><path d="M80 10v18M73 21l7 7 7-7" stroke="var(--blue)" stroke-width="2" fill="none"/></svg>
</section>

<section class="section welcome">
  <div class="abs welcome-kicker">Welcome to</div>
  <h2 class="abs welcome-title" style="font-weight:400">Brightwater Civic Advisors</h2>
  <p class="abs welcome-text">Brightwater Civic Advisors supports nonprofit organizations and educational institutions to carry out their missions to benefit the wider community. Founder Dana Whitlock is an educator with a 22-year record of demonstrated achievement and leadership roles in nonprofits and educational institutions. Most recently, she served as Associate Dean of Students in the University and Director of the University Community Service Center.</p>
  <div class="btn btn-outline" style="left:143px;top:410px;width:140px;height:38px">Read More</div>
  <div class="abs portrait-frame"></div>
  <div class="abs portrait" role="img" aria-label="Portrait of the founder"></div>
</section>

<section class="section services">
  <h2 class="abs heading" style="top:78px">Our Services</h2>
  <div class="rule" style="top:145px"></div>
  <div class="abs svc-nav" style="left:84px"><svg width="12" height="12" viewBox="0 0 12 12"><path d="M8 2L4 6l4 4" stroke="#9aa0ab" stroke-width="1.6" fill="none"/></svg></div>
  <div class="abs svc-nav" style="left:1084px"><svg width="12" height="12" viewBox="0 0 12 12"><path d="M4 2l4 4-4 4" stroke="#9aa0ab" stroke-width="1.6" fill="none"/></svg></div>
  <div class="abs svc-icons">
    <div class="svc" style="left:100px"><div class="svc-circle active"><svg width="40" height="40" viewBox="0 0 40 40" fill="none" stroke="#fff" stroke-width="2"><rect x="6" y="8" width="28" height="20"/><path d="M14 34h12M20 28v6"/><circle cx="20" cy="16" r="4"/></svg></div>Staff Professional<br>Development</div>
    <div class="svc" style="left:330px"><div class="svc-circle"><svg width="40" height="40" viewBox="0 0 40 40" fill="none" stroke="#fff" stroke-width="2"><circle cx="20" cy="12" r="4"/><circle cx="10" cy="26" r="4"/><circle cx="30" cy="26" r="4"/><path d="M20 16v6M14 26h12"/></svg></div>Community Partnership<br>Development</div>
    <div class="svc" style="left:563px"><div class="svc-circle"><svg width="40" height="40" viewBox="0 0 40 40" fill="none" stroke="#fff" stroke-width="2"><rect x="7" y="7" width="26" height="18"/><circle cx="14" cy="31" r="3"/><circle cx="26" cy="31" r="3"/><path d="M12 19l5-5 4 4 6-6"/></svg></div>Group Facilitation and<br>Leadership Training</div>
    <div class="svc" style="left:828px"><div class="svc-circle"><svg width="40" height="40" viewBox="0 0 40 40" fill="none" stroke="#fff" stroke-width="2"><rect x="9" y="6" width="22" height="28"/><path d="M14 14h12M14 20h12M14 26h8"/></svg></div>Program Design,<br>Implementation &amp; Evaluation</div>
  </div>
  <div class="abs feature-frame"></div>
  <div class="abs feature-photo" role="img" aria-label="Staff members posing together at a professional development workshop"></div>
  <h3 class="abs feature-title" style="font-weight:400">Staff Professional Development</h3>
  <p class="abs feature-text">Dana has supervised, coached, and mentored hundreds of staff members, including professionals and students. She uses the "scaffold-model-coach-fade" approach to empower and guide her staff in their personal and professional growth. She has led professional development workshops and staff retreats.</p>
  <div class="btn btn-outline" style="left:615px;top:720px;width:155px;height:42px;font-size:14px;letter-spacing:1px">LEARN MORE</div>
</section>

<section class="section testimonials">
  <h2 class="abs heading" style="top:62px">Testimonials</h2>
  <div class="rule" style="top:130px"></div>
  <div class="avatar" style="left:145px;top:195px" role="img" aria-label="Portrait of Marcus Ellery"></div>
  <div class="qmark" style="left:183px;top:328px">&#8221;</div>
  <div class="quote" style="left:288px;top:195px">
    <p class="quote-text">Sed ut perspiciatis unde omnis iste natus error sit voluptatem accusantium loremque laudantium, totam rem aperiam, eaque ipsa quae ab illo inventore</p>
    <div class="stars">★★★★★</div>
    <div class="quote-name">Marcus Ellery, Chief Executive Officer</div>
  </div>
  <div class="avatar" style="left:633px;top:195px" role="img" aria-label="Portrait of Owen Pratt"></div>
  <div class="qmark" style="left:671px;top:328px">&#8221;</div>
  <div class="quote" style="left:776px;top:195px">
    <p class="quote-text">Sed ut perspiciatis unde omnis iste natus error sit voluptatem accusantium loremque laudantium, totam rem aperiam, eaque ipsa quae ab illo inventore</p>
    <div class="stars">★★★★★</div>
    <div class="quote-name">Owen Pratt, Assistant Director</div>
  </div>
</section>

<section class="section media">
  <h2 class="abs heading" style="top:60px">Media &amp; Impact</h2>
  <div class="rule" style="top:128px"></div>
  <div class="card-photo" style="left:143px;top:203px;width:430px;height:420px" role="img" aria-label="Workshop participants seated around tables"></div>
  <div class="card" style="left:232px;top:455px;width:341px;height:168px;padding:22px 24px">
    <div class="card-title">Nemo enim ipsam voluptatem quia voluptas</div>
    <div class="card-meta"><span>Jan 25, 2018</span><span>2 comments</span></div>
    <div class="card-text">Sed ut perspiciatis unde omnis iste natus error sit voluptatem accusantium doloremque</div>
  </div>
  <div class="card" style="left:605px;top:203px;width:450px;height:200px">
    <div class="card-photo" style="left:0;top:0;width:190px;height:200px" role="img" aria-label="Group gathered on a campus lawn"></div>
    <div class="abs" style="left:210px;top:18px;width:225px">
      <div class="card-title">Nemo enim ipsam volupta quia voluptas</div>
      <div class="card-meta"><span>Jan 25, 2018</span><span>2 comments</span></div>
      <div class="card-text">Sed ut perspiciatis unde omnis iste natus error sit volupt accusan-tium doloremque</div>
    </div>
  </div>
  <div class="card" style="left:605px;top:430px;width:450px;height:200px">
    <div class="card-photo" style="left:0;top:0;width:190px;height:200px" role="img" aria-label="Participants in an indoor team activity"></div>
    <div class="abs" style="left:210px;top:18px;width:225px">
      <div class="card-title">Nemo enim ipsam volupta quia voluptas</div>
      <div class="card-meta"><span>Jan 25, 2018</span><span>2 comments</span></div>
      <div class="card-text">Sed ut perspiciatis unde omnis iste natus error sit volupt accusan-tium doloremque</div>
    </div>
  </div>
</section>

<section class="section partners">
  <div class="badge" style="left:210px;top:85px;width:100px;height:100px;border-radius:50%"></div>
  <div class="badge" style="left:365px;top:97px;width:265px;height:78px"></div>
  <div class="badge" style="left:695px;top:85px;width:90px;height:100px;border-radius:50%"></div>
  <div class="badge" style="left:830px;top:100px;width:240px;height:72px"></div>
  <div class="badge" style="left:245px;top:237px;width:320px;height:55px"></div>
  <div class="badge" style="left:730px;top:240px;width:205px;height:48px"></div>
</section>

<section class="section contact">
  <svg class="abs contact-notch" viewBox="0 0 90 32"><path d="M0 0 C25 0 35 32 45 32 C55 32 65 0 90 0Z" fill="#fff"/></svg>
  <svg class="abs" style="left:588px;top:-24px" width="24" height="30" viewBox="0 0 24 30"><path d="M12 28V4M4 12l8-8 8 8" stroke="var(--navy-deep)" stroke-width="2.5" fill="none"/></svg>
  <h2 class="abs heading" style="top:95px">Contact Us</h2>
  <div class="rule" style="top:160px"></div>
  <div class="info-row" style="top:210px"><div class="info-icon"><svg width="18" height="18" viewBox="0 0 24 24" fill="#fff"><path d="M12 2a7 7 0 0 0-7 7c0 5 7 13 7 13s7-8 7-13a7 7 0 0 0-7-7zm0 9.5A2.5 2.5 0 1 1 12 6.5a2.5 2.5 0 0 1 0 5z"/></svg></div><div>Brightwater Civic Advisors<br>2450 Harbor Ln. Fairview,<br>ST 10422</div></div>
  <div class="info-row" style="top:295px"><div class="info-icon"><svg width="16" height="16" viewBox="0 0 24 24" fill="#fff"><path d="M6.6 10.8a15.1 15.1 0 0 0 6.6 6.6l2.2-2.2a1 1 0 0 1 1-.25 11.4 11.4 0 0 0 3.6.57 1 1 0 0 1 1 1V20a1 1 0 0 1-1 1A17 17 0 0 1 3 4a1 1 0 0 1 1-1h3.5a1 1 0 0 1 1 1c0 1.25.2 2.45.57 3.57a1 1 0 0 1-.25 1z"/></svg></div><div>Phone :<br>555-010-4821</div></div>
  <div class="info-row" style="top:370px"><div class="info-icon"><svg width="16" height="18" viewBox="0 0 16 18" fill="none" stroke="#fff" stroke-width="2"><rect x="3" y="1" width="10" height="16" rx="1.5"/></svg></div><div>Fax :<br>555-010-7390</div></div>
  <div class="info-row" style="top:445px"><div class="info-icon"><svg width="18" height="14" viewBox="0 0 18 14" fill="none" stroke="#fff" stroke-width="2"><rect x="1" y="1" width="16" height="12"/><path d="M1 1l8 6 8-6"/></svg></div><div>Email :<br>info@brightwatercivic.example</div></div>
  <div class="field" style="left:520px;top:207px;width:260px;height:40px">Your Name</div>
  <div class="field" style="left:800px;top:207px;width:255px;height:40px">Your Email</div>
  <div class="field" style="left:520px;top:272px;width:260px;height:40px">Your Phone/Mobile</div>
  <div class="field" style="left:800px;top:272px;width:255px;height:40px">Subject</div>
  <div class="field" style="left:520px;top:337px;width:535px;height:105px">Your Message</div>
  <div class="btn btn-solid" style="left:520px;top:460px;width:178px;height:40px;font-size:13px;font-weight:500;letter-spacing:.5px">SEND MESSAGES</div>
</section>

<footer class="section footer">
  <div class="abs foot-links">About &nbsp;|&nbsp; Services &amp; Testimonials &nbsp;|&nbsp; Media &amp; Impact &nbsp;|&nbsp; Contact</div>
  <div class="abs foot-copy">Brightwater Civic Advisors © 2019 All Rights Reserved.</div>
  <div class="social" style="left:540px"></div>
  <div class="social" style="left:585px"></div>
  <div class="social" style="left:630px;border-color:#d9534f"></div>
</footer>

</body>
</html>
```